Lone Star Wetland Flora Stewardship Guild

We need to design the home page of this new website. We would like a fun website design for provides as a resource for members and information for potential members.
Please design so that we can see a portion of background on each side on the website.
I just need the final design files psd no coding needed.
Attached is their logo (colors are not 100% set in stone either so can mess with those as I did in the quick mockup attached)
Attached is a pdf newsletter they send out, you can get a feel for them and what they are about. The design is crappy and we are here to fix that going forward and we are starting with the website.
Here are some quick example websites (design style is open)
- I attached a quick mockup i did just for a content visual but by all means do what you want.
- http://www.brightpathleaders.example/
- http://www.civicunityhub.example/
- http://preview.webskinvault.example/show.php?cat=layouts&host=skinbazaar&temp=novaline
- http://www.meadowkeep.example/
- http://www.urbangleaners.example/
- http://www.projectcozyknit.example/
here are some of the other chapters website (pretty bad!)
and here are some of the others:
- http://www.dwrvcs.example/
- http://kwfg.example/
- http://www.blvcg.example/
Content Items that need to be included:
1. Logo
2. Menu - home, about, members, resources, events, membership, contact
3. Become a member - button or action
4. social links - chatterloop, workweave, clipstream
5. banner - that needs to explain their purpose "Promoting environmental stewardship through operations, research, education and outreach" (or this can be worked into the design)
6. Upcoming event (s)
7. Advertisement - members can place an ad on the website, this can be a placeholder for now
8. newsletter signup
9. advertise with us - this link can be in the footer
30-60 years of age, succesfull (household budgets of 120K+ men and women that live in texas.
Education

```html
<!DOCTYPE html>
<html lang="en">
<head>
<meta charset="utf-8">
<title>Lone Star Wetland Flora Stewardship Guild</title>
<link rel="stylesheet" href="https://fonts.googleapis.com/css2?family=Tinos:wght@400;700&display=swap">
<style>
:root{
  --navy:#0b3f8f;
  --navy-dark:#093477;
  --red:#d84657;
  --green:#00b07b;
  --ink:#1e1e1e;
  --panel:#f4f4f4;
  --bar:#1c1c1c;
  --white:#ffffff;
}
*{box-sizing:border-box;margin:0;padding:0}
html,body{width:1113px;height:1200px;overflow:hidden}
body{position:relative;font-family:"Tinos",serif;color:var(--ink);background:var(--white)}
a{color:inherit;text-decoration:none}
.landscape-bg{position:absolute;left:0;top:0;width:1113px;height:600px;
  background:linear-gradient(180deg,#8fb7d8 0%,#b8d2e6 14%,#a9c4d8 18%,#6f9a4e 24%,#7fa85a 34%,#5d87b3 46%,#8fb0c9 62%,rgba(255,255,255,0.6) 80%,#fff 100%)}
.top-bar{position:absolute;left:116px;top:28px;width:881px;height:32px;display:flex;justify-content:flex-end;align-items:center}
.top-bar .society{font-size:13px;margin-right:8px;color:#222}
.btn-member{background:var(--navy);color:var(--white);font-weight:700;font-size:14px;height:32px;line-height:32px;padding:0 9px;margin-right:3px}
.btn-login{background:var(--red);color:var(--white);font-weight:700;font-size:14px;height:32px;line-height:32px;padding:0 14px}
.site-header{position:absolute;left:116px;top:60px;width:881px;height:95px;background:var(--white);display:flex;align-items:center}
.brand{display:flex;align-items:center;gap:8px;margin-left:12px;width:170px}
.brand-dot{width:14px;height:14px;border-radius:50%;background:var(--red);flex:none}
.brand-name{font-size:14px;font-weight:700;color:var(--navy);line-height:16px}
.main-nav{display:flex;gap:0;margin-left:29px}
.main-nav a{font-size:16px;font-weight:700;color:#2a2a2a;margin-right:39px}
.main-nav a.current{color:var(--navy)}
.main-nav a:last-child{margin-right:0}
.hero{position:absolute;left:116px;top:155px;width:881px;height:332px;
  background:linear-gradient(180deg,#7ea9d1 0%,#c6dcec 30%,#a9c7df 42%,#6d9a48 50%,#8fb25b 58%,#4f7fae 70%,#6f98c0 86%,#5a86b3 100%)}
.hero-caption{position:absolute;left:16px;top:115px;width:352px;height:152px;background:rgba(40,40,40,0.82);padding:22px 22px 0 23px}
.hero-caption h1{font-weight:400;font-size:23px;line-height:30px;color:var(--white)}
.slide-dots{display:flex;gap:5px;margin-top:12px}
.slide-dots span{width:9px;height:9px;border-radius:50%;background:var(--white)}
.slide-dots span.active{background:var(--red)}
.newsletter{position:absolute;left:116px;top:487px;width:881px;height:74px;background:var(--bar)}
.newsletter .mail-icon{position:absolute;left:34px;top:28px}
.newsletter label{position:absolute;left:69px;top:27px;color:var(--white);font-weight:700;font-size:15px}
.newsletter .email-field{position:absolute;left:210px;top:20px;width:535px;height:32px;background:#232323;border:1px solid #3a3a3a;color:#777;font-size:12px;line-height:30px;padding-left:9px}
.newsletter .btn-signup{position:absolute;left:756px;top:20px;width:113px;height:32px;background:var(--red);color:var(--white);font-weight:700;font-size:15px;line-height:32px;text-align:center}
.section-title{position:absolute;top:649px;font-size:14px;font-weight:700;color:var(--red)}
.panel{position:absolute;top:673px;background:var(--panel)}
.about-panel{left:116px;width:287px;height:369px;padding:22px 14px 0 16px;font-size:13.5px;line-height:22.3px;letter-spacing:-0.3px}
.events-panel{left:412px;width:288px;height:369px}
.event{position:absolute;left:9px;display:flex}
.event-thumb{width:90px;height:66px;flex:none;background:linear-gradient(180deg,#8fb36b,#4b7a3c 60%,#3f6a5a)}
.event-text{margin-left:12px;width:170px;font-size:12.3px;line-height:16.5px;letter-spacing:-0.3px}
.event-text strong{display:block}
.btn-small{position:absolute;top:1042px;height:25px;line-height:25px;background:var(--red);color:var(--white);font-weight:700;font-size:13px;text-align:center}
.ad-panel{left:710px;width:287px;height:394px;background:#ececec}
.ad-brand{position:absolute;left:13px;top:13px;display:flex;align-items:center;gap:6px;font-size:26px;font-weight:700;line-height:26px;color:#222}
.ad-brand .dot{width:16px;height:16px;border-radius:50%;background:#2e8fb0}
.ad-product{position:absolute;left:50px;top:88px;width:190px;height:210px;border-radius:10px;background:linear-gradient(180deg,#ffffff,#e4e8ec 70%,#cfd6dd)}
.ad-strip{position:absolute;left:0;top:317px;width:287px;height:77px;background:var(--green);color:var(--white)}
.ad-strip p{position:absolute;left:17px;top:12px;width:160px;font-size:13px;line-height:17px;font-weight:700}
.ad-strip p span{display:block;font-weight:400;font-size:12px}
.ad-strip .btn-click{position:absolute;left:184px;top:22px;width:94px;height:34px;border-radius:6px;background:var(--navy);font-weight:700;font-size:17px;line-height:34px;text-align:center}
.site-footer{position:absolute;left:0;top:1106px;width:1113px;height:94px;background:var(--navy);color:var(--white)}
.footer-nav{position:absolute;left:122px;top:29px;display:flex;font-size:13px;font-weight:700}
.footer-nav a::after{content:"|";margin:0 17px;font-weight:400}
.footer-nav a:last-child::after{content:none}
.copyright{position:absolute;left:122px;top:57px;font-size:13px;font-weight:700}
.advertise{position:absolute;left:724px;top:45px;font-size:14px;font-weight:700;text-decoration:underline}
.social{position:absolute;left:926px;top:38px;display:flex;gap:3px}
.social a{width:21px;height:21px;border-radius:50%;background:var(--white)}
</style>
</head>
<body>
<div class="landscape-bg" role="img" aria-label="Wide wetland landscape with blue sky, clouds, green marsh grass and open water fading to white"></div>

<div class="top-bar">
  <span class="society">Lone Star Wetland Flora Stewardship Guild</span>
  <a class="btn-member" href="#">Become A Member</a>
  <a class="btn-login" href="#">Login</a>
</div>

<header class="site-header">
  <a class="brand" href="#">
    <span class="brand-dot"></span>
    <span class="brand-name">Lone Star Wetland Flora Stewardship Guild</span>
  </a>
  <nav class="main-nav">
    <a class="current" href="#">Home</a>
    <a href="#">About</a>
    <a href="#">Members</a>
    <a href="#">Resources</a>
    <a href="#">Events</a>
    <a href="#">Membership</a>
    <a href="#">Contact</a>
  </nav>
</header>

<section class="hero" role="img" aria-label="Photo of a Texas wetland: marsh grass and reflective water under a cloudy blue sky">
  <div class="hero-caption">
    <h1>Promoting environmental stewardship through operations, research, education and outreach</h1>
    <div class="slide-dots"><span class="active"></span><span></span><span></span><span></span></div>
  </div>
</section>

<form class="newsletter">
  <svg class="mail-icon" width="27" height="18" viewBox="0 0 27 18" aria-hidden="true">
    <rect width="27" height="18" fill="#d84657"/>
    <path d="M0 0 L13.5 10 L27 0 M0 18 L10 8 M27 18 L17 8" stroke="#fff" stroke-width="1.6" fill="none"/>
  </svg>
  <label>Newsletter Sign Up</label>
  <div class="email-field">Enter Your E-mail Address</div>
  <a class="btn-signup" href="#">Sign Up</a>
</form>

<h2 class="section-title" style="left:117px">About LSWFSG</h2>
<h2 class="section-title" style="left:413px">Upcoming Events</h2>
<h2 class="section-title" style="left:711px">Advertisement</h2>

<article class="panel about-panel">
  Lorem Ipsum is simply dummy text of the printing and typesetting industry. Lorem Ipsum has been the industry's standard dummy text ever since the 1500s, when an unknown printer took a galley of type and scrambled it to make a type specimen book. It has survived not only five centuries, but also the leap into electronic typesetting, remaining essentially unchanged.Lorem Ipsum is simply dummy text of the printing and typesetting industry. Lorem Ipsum has been the industry's standard dummy text ever since the 1500s, when an unknown printer took a galley of type and scrambled it to make a type specimen book.
</article>
<a class="btn-small" href="#" style="left:321px;width:82px">Read More</a>

<section class="panel events-panel">
  <div class="event" style="top:26px">
    <div class="event-thumb" role="img" aria-label="Pond with lily pads and reeds"></div>
    <div class="event-text"><strong>Lorem Ipsum is simply dummy text of the printing</strong>Lorem Ipsum has been the industry's standard dummy text ever s</div>
  </div>
  <div class="event" style="top:143px">
    <div class="event-thumb" role="img" aria-label="River bank with green trees and water"></div>
    <div class="event-text"><strong>Lorem Ipsum is simply dummy text of the printing</strong>Lorem Ipsum has been the industry's standard dummy text ever s</div>
  </div>
  <div class="event" style="top:259px">
    <div class="event-thumb" role="img" aria-label="Lake with floating water lilies and trees"></div>
    <div class="event-text"><strong>Lorem Ipsum is simply dummy text of the printing</strong>Lorem Ipsum has been the industry's standard dummy text ever s</div>
  </div>
</section>
<a class="btn-small" href="#" style="left:618px;width:82px">View All</a>

<aside class="panel ad-panel">
  <div class="ad-brand"><span class="dot"></span>Marshline Supply</div>
  <div class="ad-product" role="img" aria-label="Product photo of a white pail of pond treatment tablets"></div>
  <div class="ad-strip">
    <p>Lorem Ipsum is simply dummy text of the printing<span>Lorem Ipsum has been</span></p>
    <a class="btn-click" href="#">Click Here</a>
  </div>
</aside>

<footer class="site-footer">
  <nav class="footer-nav">
    <a href="#">Home</a><a href="#">About</a><a href="#">Members</a><a href="#">Resources</a><a href="#">Events</a><a href="#">Membership</a><a href="#">Contact</a>
  </nav>
  <p class="copyright">© Compnay Name ,All Rights Reserved</p>
  <a class="advertise" href="#">Advertise With Us !</a>
  <div class="social">
    <a href="#" aria-label="chatterloop"></a>
    <a href="#" aria-label="workweave"></a>
    <a href="#" aria-label="clipstream"></a>
  </div>
</footer>
</body>
</html>
```